Ridge Lass Crew (Flyer)

I want a flyer to advertise my service.
Details below, and logo's to use are attached.

A girls only after school program, 11-14yrs, as OSHC is no longer avail, dedicated to coaching & mentoring our girls into strong, independent young women.

The Brainchild of Rebecca Folwin, Ridge Lass Crew was created to address the growing demand for after school/school holiday supervision for kids moving from primary into high school, when OSHC ceases to exist.
With over 12 years experience mentoring and coaching young women in the corporate world, Bec decided to leave her role as a Director with Tarrant Trust, and follow her passion.
Bec, along with her sister Lorraine, who has over 10 years experience in local communities as a Youth Worker, and is also a qualified Enrolled Nurse, embarked on building a program designed to keep parents happy (by knowing their girls are safe) and dedicated to coaching and mentoring our girls into strong, independent young women.
Open every afternoon and during school holidays, we look to offer;
- Daily meditation
- Healthy snacks
- Dedicated homework time
- Organised group activity, led by qualified instructors (yoga, fitness class, soccer etc)
- Regular guests speakers, addressing issues/concerns for young people today
- SOCIAL MEDIA FREE ZONE

Located 87 Pelham Pde, Baulkham Hills (across from Crestmoor Day Clinic)
Open 3-6pm Monday to Friday

Facebook page: http://fb.example/ridgelasscrew
Email: info@ridgelasscrew.example.au
Mobile: 0455817396

Target Market(s)

Parents of teenage girls, teenage girls 11-14 years

Industry/Entity Type

School

Font styles to use
Sans Serif

Colors
b768aa
e667a6

Requirements
Must have
• What progam is - see brief
• Who runs it
Should not have
• Not be too busy, not overly mature images

```html
<!DOCTYPE html>
<html lang="en">
<head>
<meta charset="utf-8">
<title>Ridge Lass Crew – After School Program Flyer</title>
<link rel="stylesheet" href="https://fonts.googleapis.com/css2?family=Cinzel:wght@700&family=Open+Sans:wght@400;600;700&family=Roboto+Condensed:wght@300&display=swap">
<style>
  :root {
    --magenta: #e94fe6;
    --pink: #e667a6;
    --orchid: #b768aa;
    --violet: #b65ae8;
    --bullet: #c46de8;
    --ink: #111111;
    --navy: #2b3550;
    --white: #ffffff;
  }
  * { margin: 0; padding: 0; box-sizing: border-box; }
  html, body { width: 934px; height: 1200px; overflow: hidden; background: var(--white); }
  .flyer { position: relative; width: 934px; height: 1200px; overflow: hidden; background: var(--white); font-family: "Open Sans", Arial, sans-serif; color: var(--ink); }
  .backdrop, .scene { position: absolute; left: 0; top: 0; width: 934px; height: 1200px; }
  .scene { z-index: 3; }

  .brand-name {
    position: absolute; left: 30px; top: 110px; width: 230px;
    font-family: "Open Sans", Arial, sans-serif; font-weight: 700;
    font-size: 44px; line-height: 52px; color: var(--magenta); text-align: center;
  }

  .headline { position: absolute; font-family: "Cinzel", Georgia, serif; font-weight: 700; color: var(--ink); white-space: nowrap; }
  .headline--one { left: 300px; top: 46px; font-size: 35px; }
  .headline--two { left: 482px; top: 90px; font-size: 35px; }
  .age-line { position: absolute; left: 302px; top: 134px; white-space: nowrap; }
  .age-line .ages { font-family: "Cinzel", Georgia, serif; font-weight: 700; font-size: 32px; color: #c23ad3; text-shadow: 1px 1px 0 #3a1a3e; }
  .age-line .reason { font-weight: 600; font-size: 19px; color: var(--magenta); margin-left: 8px; }

  .founder { position: absolute; left: 270px; width: 660px; text-align: center; font-family: "Cinzel", Georgia, serif; font-weight: 700; font-size: 30px; white-space: nowrap; }
  .founder--name { top: 236px; }
  .founder--crew { top: 298px; }

  .section-title { position: absolute; font-weight: 700; font-size: 24px; color: var(--navy); }
  .who-title { left: 72px; top: 374px; }
  .offer-title { left: 588px; top: 366px; }
  .who-text { position: absolute; left: 68px; top: 412px; width: 380px; font-size: 19.5px; line-height: 30px; }

  .offer-list { position: absolute; left: 578px; top: 404px; list-style: none; font-size: 19.5px; }
  .offer-list li { position: relative; padding-left: 18px; line-height: 30px; white-space: nowrap; }
  .offer-list li::before { content: ""; position: absolute; left: 0; top: 12px; width: 8px; height: 8px; border-radius: 50%; background: var(--bullet); }
  .offer-list .sub { padding-left: 47px; }
  .offer-list .sub::before { display: none; }
  .offer-list .gap { margin-top: 7px; }

  .contact { position: absolute; color: var(--white); white-space: nowrap; z-index: 4; }
  .contact svg { position: absolute; }
  .contact-phone { left: 18px; top: 626px; font-size: 21px; line-height: 30px; }
  .contact-phone span { margin-left: 38px; }
  .contact-address { left: 18px; top: 664px; }
  .contact-address .line { display: block; font-family: "Roboto Condensed", "Arial Narrow", sans-serif; font-weight: 300; font-size: 22px; line-height: 26px; margin-left: 32px; }
  .contact-address .line + .line { font-family: "Open Sans", Arial, sans-serif; font-weight: 400; font-size: 20px; margin-left: 50px; }
  .contact-hours { left: 18px; top: 720px; font-size: 18px; font-weight: 600; line-height: 24px; }
  .contact-hours span { margin-left: 32px; }
  .contact-mail { left: 16px; top: 748px; font-size: 18px; font-weight: 600; line-height: 25px; }
  .contact-mail span { display: block; margin-left: 36px; }
  .contact-web { left: 16px; top: 802px; font-size: 18px; font-weight: 600; line-height: 24px; }
  .contact-web .square { display: inline-block; width: 18px; height: 18px; background: #3b82e0; vertical-align: -3px; margin-right: 14px; }
</style>
</head>
<body>
<main class="flyer">
  <svg class="backdrop" viewBox="0 0 934 1200" aria-hidden="true">
    <path d="M590,0 C700,40 820,70 934,72 L934,0 Z" fill="var(--magenta)"/>
    <path d="M0,632 C260,580 600,590 934,790 C760,760 400,810 0,930 Z" fill="var(--violet)"/>
  </svg>

  <div class="brand-name">Ridge Lass Crew</div>

  <h1 class="headline headline--one">A Girls Only After</h1>
  <div class="headline headline--two">School Program</div>
  <p class="age-line"><span class="ages">For 11-14yrs</span><span class="reason">as OSHC is no longer available</span></p>

  <h2 class="founder founder--name">The Brainchild of Rebecca Folwin</h2>
  <div class="founder founder--crew">Ridge Lass Crew</div>

  <h3 class="section-title who-title">WHO WE ARE</h3>
  <p class="who-text">The Brainchild of Rebecca Folwin, Ridge Lass Crew was created to address the growing demand for after school/school holiday supervision for kids moving from primary into high school, when OSHC ceases to exist.</p>

  <h3 class="section-title offer-title">WHAT WE OFFER</h3>
  <ul class="offer-list">
    <li>Daily meditation</li>
    <li>Healthy snacks</li>
    <li>Organised group activity,</li>
    <li class="sub">(yoga, fitness class, soccer etc.)</li>
    <li class="gap">Regular guests speakers</li>
    <li>Dedicated homework time</li>
    <li>Social media free zone</li>
  </ul>

  <div class="contact contact-phone">
    <svg width="28" height="28" viewBox="0 0 24 24" style="left:0;top:1px" fill="none" stroke="#fff" stroke-width="1.8" stroke-linejoin="round"><path d="M5 3h4l2 5-2.5 1.5a11 11 0 0 0 6 6L16 13l5 2v4a2 2 0 0 1-2 2A17 17 0 0 1 3 5a2 2 0 0 1 2-2z"/></svg>
    <span>Call: 0455817396</span>
  </div>
  <div class="contact contact-address">
    <svg width="22" height="30" viewBox="0 0 22 30" style="left:2px;top:0" fill="none" stroke="#fff" stroke-width="2"><path d="M11 28C4 18 2 14 2 10a9 9 0 0 1 18 0c0 4-2 8-9 18z"/><circle cx="11" cy="10" r="3.5"/></svg>
    <span class="line">87 Pelham Pde, Baulkham Hills</span>
    <span class="line">(across from Crestmoor Day Clinic)</span>
  </div>
  <div class="contact contact-hours">
    <svg width="22" height="22" viewBox="0 0 22 22" style="left:1px;top:1px" fill="none" stroke="#fff" stroke-width="1.8" stroke-linecap="round"><circle cx="11" cy="11" r="9"/><path d="M11 6v5l3 2"/></svg>
    <span>Open 3-6pm Monday to Friday</span>
  </div>
  <div class="contact contact-mail">
    <svg width="24" height="26" viewBox="0 0 24 26" style="left:2px;top:2px" fill="none" stroke="#fff" stroke-width="1.8" stroke-linejoin="round"><path d="M2 10L12 2l10 8v14H2z"/><path d="M2 10l10 7 10-7M2 24l8-7M22 24l-8-7"/></svg>
    <span>e-Mail us</span>
    <span>info@ridgelasscrew.example.au</span>
  </div>
  <div class="contact contact-web"><span class="square"></span>http://fb.example/ridgelasscrew</div>

  <svg class="scene" viewBox="0 0 934 1200" role="img" aria-label="Photo of a girl sitting cross-legged on a pink yoga mat among dune grass, looking out over the sea">
    <defs>
      <linearGradient id="sceneTones" x1="0" y1="0" x2="0" y2="1">
        <stop offset="0" stop-color="#7a6bd8"/>
        <stop offset="0.22" stop-color="#8b86d2"/>
        <stop offset="0.42" stop-color="#5f8a4c"/>
        <stop offset="0.68" stop-color="#d6d0bf"/>
        <stop offset="1" stop-color="#e4d3dc"/>
      </linearGradient>
    </defs>
    <path d="M0,1110 C150,850 500,760 934,880 L934,1200 L0,1200 Z" fill="url(#sceneTones)"/>
  </svg>
</main>
</body>
</html>
```